Vantiqo custom business card design

Need a authentic, innovative business card design for a new mobile app business. I am uploading a few screen images from our app for you to view. I would like app design theme to match business card design. I can also send logo images.

```html
<!DOCTYPE html>
<html lang="en">
<head>
<meta charset="utf-8">
<title>Vantiqo Business Card</title>
<link href="https://fonts.googleapis.com/css2?family=Montserrat:wght@300;400;600;800&display=swap" rel="stylesheet">
<style>
  :root {
    --stage: #2b2b2d;
    --card-white: #ffffff;
    --card-black: #141414;
    --ink: #111111;
    --ink-soft: #2a2a2a;
    --purple: #6a1fa8;
    --purple-light: #8a4fc4;
    --grey-mark: #5a5a5a;
  }
  * { box-sizing: border-box; margin: 0; padding: 0; }
  html, body {
    width: 1200px;
    height: 716px;
    overflow: hidden;
    background: var(--stage);
    font-family: "Montserrat", sans-serif;
  }
  .stage {
    position: relative;
    width: 1200px;
    height: 716px;
    display: flex;
    align-items: center;
    justify-content: center;
    gap: 60px;
  }
  .card {
    position: relative;
    width: 520px;
    height: 297px;
    border-radius: 18px;
    overflow: hidden;
  }
  /* Back side */
  .card--back {
    background: var(--card-black);
  }
  .back-brand {
    position: absolute;
    left: 50%;
    top: 50%;
    transform: translate(-50%, -50%);
    display: flex;
    align-items: center;
    gap: 14px;
  }
  .back-brand .brand-dot {
    width: 26px;
    height: 26px;
    border-radius: 50%;
    background: var(--purple);
  }
  .back-brand .brand-name {
    font-weight: 800;
    font-size: 36px;
    color: var(--grey-mark);
    letter-spacing: 0.5px;
  }
  /* Front side */
  .card--front {
    background: var(--card-white);
  }
  .identity {
    position: absolute;
    left: 34px;
    top: 30px;
  }
  .identity .person-name {
    font-weight: 800;
    font-size: 22px;
    color: var(--ink);
    line-height: 1.1;
  }
  .identity .job-title {
    font-weight: 300;
    font-size: 13px;
    color: var(--purple);
    margin-top: 2px;
  }
  .identity .title-rule {
    width: 50px;
    height: 1.5px;
    background: var(--purple);
    margin-top: 5px;
  }
  .contacts {
    position: absolute;
    left: 34px;
    bottom: 34px;
    list-style: none;
  }
  .contacts li {
    display: flex;
    align-items: center;
    gap: 12px;
    font-size: 12.5px;
    font-weight: 400;
    color: var(--ink-soft);
    height: 22px;
  }
  .contacts svg {
    width: 13px;
    height: 13px;
    flex: none;
  }
  .front-brand {
    position: absolute;
    right: 34px;
    bottom: 36px;
    display: flex;
    align-items: center;
    gap: 10px;
  }
  .front-brand .brand-dot {
    width: 22px;
    height: 22px;
    border-radius: 50%;
    background: var(--purple);
  }
  .front-brand .brand-name {
    font-weight: 800;
    font-size: 30px;
    color: var(--ink);
  }
</style>
</head>
<body>
<main class="stage">
  <section class="card card--back" aria-label="Card back">
    <div class="back-brand">
      <span class="brand-dot"></span>
      <span class="brand-name">Vantiqo</span>
    </div>
  </section>

  <section class="card card--front" aria-label="Card front">
    <div class="identity">
      <p class="person-name">Your Name</p>
      <p class="job-title">Job Title</p>
      <div class="title-rule"></div>
    </div>

    <ul class="contacts">
      <li>
        <svg viewBox="0 0 14 14" aria-hidden="true"><rect x="3.5" y="1" width="7" height="12" rx="1.2" fill="none" stroke="var(--purple)" stroke-width="1.3"/><line x1="6" y1="11" x2="8" y2="11" stroke="var(--purple)" stroke-width="1.2"/></svg>
        000 000 0000
      </li>
      <li>
        <svg viewBox="0 0 14 14" aria-hidden="true"><rect x="1" y="3" width="12" height="8.5" fill="var(--purple)"/><polyline points="1,3 7,8 13,3" fill="none" stroke="#ffffff" stroke-width="1"/></svg>
        youremail@xyz.com
      </li>
      <li>
        <svg viewBox="0 0 14 14" aria-hidden="true"><circle cx="7" cy="7" r="5.5" fill="none" stroke="var(--purple-light)" stroke-width="1.1"/><ellipse cx="7" cy="7" rx="2.4" ry="5.5" fill="none" stroke="var(--purple-light)" stroke-width="1"/><line x1="1.5" y1="7" x2="12.5" y2="7" stroke="var(--purple-light)" stroke-width="1"/></svg>
        www.yourwebsite.com
      </li>
    </ul>

    <div class="front-brand">
      <span class="brand-dot"></span>
      <span class="brand-name">Vantiqo</span>
    </div>
  </section>
</main>
</body>
</html>
```